Accountability Project Graphics

I want to create 10 social media graphics (new Instagram size 4:5 (1080 x 1350 pixels) focusing on our Quilvo Accountability App, using any of the 3 pictures attached. Use the attached pics only, NO RANDOM STOCK PHOTOGRAPHY. For the color scheme, use the landing page colors/fonts (attached).
You can add any of the 3 photos attached but I mainly need BOLD text that includes these headlines and sub-headlines on them.
Please NOTE for all the headlines below, also add this sub-headline on each graphic:
Stay Consistent with RT in Your Pocket!
Here are the headlines:
• Stop Starting Over Every Monday
• You don't need more willpower. You need more support
• Built for women who are tired of doing this alone
• When Motivation Fades, RT Checks In
• The Support System You've Been Missing
• Support When Motivation Disappears
• What if RT Checked in Every Day?
• The Missing Piece Isn't Another Diet
• Eat the food you love. Stay accountable every day.
• One Bad Meal Doesn't Mean You Failed
women over 40 trying to lose weight

```html
<!DOCTYPE html>
<html lang="en">
<head>
<meta charset="utf-8">
<title>Accountability Graphics Set</title>
<link rel="stylesheet" href="https://fonts.googleapis.com/css2?family=Playfair+Display:ital,wght@0,700;0,800;1,700;1,800&family=Roboto+Condensed:ital,wght@1,700&display=swap">
<style>
:root{
  --board:#6b6b6b;
  --plum:#2a1433;
  --rose:#c4517a;
  --card-top:#f5d9e2;
  --card-bottom:#fdf7f8;
  --cta-dark:#3a0d33;
  --cta-light:#6e2151;
  --band:#4a1540;
  --white:#ffffff;
  --cta-rose:#e06a99;
}
*{box-sizing:border-box;margin:0;padding:0}
html,body{width:1200px;height:3484px;overflow:hidden}
body{background:var(--board);position:relative;font-family:"Playfair Display",Georgia,serif}
.card{position:absolute;width:494px;height:616px;overflow:hidden;
  background:linear-gradient(180deg,var(--card-top),var(--card-bottom));
  border-top:6px solid var(--rose)}
.col-left{left:88px}.col-right{left:630px}
.row-1{top:108px}.row-2{top:767px}.row-3{top:1426px}.row-4{top:2085px}.row-5{top:2744px}
.line{position:absolute;left:0;right:0;font-weight:800;white-space:nowrap;color:var(--plum)}
.center{text-align:center}
.rose{color:var(--rose);font-style:italic}
.photo{position:absolute}
.photo-portrait{background:radial-gradient(ellipse at 55% 40%,#2a2438 0%,#1c1a26 45%,rgba(240,215,225,0) 72%)}
.photo-hug{background:linear-gradient(120deg,#c8a7c9 0%,#3b2a4a 35%,#d35d8a 60%,#e8c9d8 100%)}
.photo-pair{background:radial-gradient(ellipse at 50% 55%,#2c3550 0%,#5a6480 40%,#c9c2c6 75%,#e6dfe2 100%)}
.photo-wide{background:linear-gradient(180deg,#d9d2d5 0%,#c8c2c6 40%,#2a2a3a 70%,#2a2a3a 100%)}
.cta{position:absolute;left:28px;width:436px;height:138px;border-radius:40px;
  background:linear-gradient(90deg,var(--cta-dark),var(--cta-light));
  font-family:"Roboto Condensed",Arial,sans-serif;font-style:italic;font-weight:700;
  font-size:37px;line-height:46px;text-align:center;color:var(--white);
  display:flex;flex-direction:column;justify-content:center}
.cta em,.band em{color:var(--cta-rose);font-style:italic}
.band{position:absolute;left:0;right:0;bottom:0;height:68px;background:var(--band);
  font-family:"Roboto Condensed",Arial,sans-serif;font-style:italic;font-weight:700;
  font-size:24px;color:var(--white);display:flex;align-items:center;justify-content:center}
.overlay{position:absolute;left:0;right:0;top:282px;bottom:68px;border-radius:34px 34px 0 0;
  background:rgba(250,238,242,.82)}
.side-band{position:absolute;left:317px;right:0;top:415px;bottom:0;background:var(--band);
  font-family:"Roboto Condensed",Arial,sans-serif;font-style:italic;font-weight:700;
  font-size:24px;line-height:31px;color:var(--white);padding:14px 0 0 16px}
</style>
</head>
<body>

<section class="card col-left row-1">
  <div class="photo photo-portrait" style="left:284px;top:14px;width:210px;height:440px" role="img" aria-label="Smiling coach in a dark lace top, hand on hip"></div>
  <div class="line" style="left:38px;top:36px;font-size:66px;line-height:74px">Stop<br>Starting<br>Over</div>
  <div class="line rose" style="left:38px;top:258px;font-size:66px;line-height:74px">Every<br>Monday</div>
  <div class="cta" style="top:452px"><span>Stay Consistent with</span><em>RT in Your Pocket!</em></div>
</section>

<section class="card col-right row-1">
  <div class="line rose center" style="top:18px;font-size:36px;line-height:50px;font-weight:700">You don't need more<br>willpower.</div>
  <div class="line center" style="top:118px;font-size:62px;line-height:66px">You need<br>More Support</div>
  <div class="photo photo-hug" style="left:0;right:0;top:250px;height:298px" role="img" aria-label="Two women sharing a joyful hug"></div>
  <div class="band"><span>Stay Consistent with&nbsp;<em>RT in Your Pocket!</em></span></div>
</section>

<section class="card col-left row-2">
  <div class="line center" style="top:42px;font-size:52px;line-height:64px">Built for women</div>
  <div class="line rose center" style="top:108px;font-size:52px;line-height:64px">who are tired of<br>doing this alone</div>
  <div class="photo photo-pair" style="left:0;right:0;top:234px;height:314px" role="img" aria-label="Two women laughing together in denim jackets"></div>
  <div class="band"><span>Stay Consistent with&nbsp;<em>RT in Your Pocket!</em></span></div>
</section>

<section class="card col-right row-2">
  <div class="photo photo-wide" style="left:0;right:0;top:0;height:548px" role="img" aria-label="Smiling coach in a dark lace top"></div>
  <div class="overlay"></div>
  <div class="line center" style="top:322px;font-size:42px;line-height:58px;font-style:italic;font-weight:700">When Motivation<br>Fades,</div>
  <div class="line rose center" style="top:446px;font-size:70px;line-height:84px;font-style:normal">RT Checks In</div>
  <div class="band"><span>Stay Consistent with&nbsp;<em>RT in Your Pocket!</em></span></div>
</section>

<section class="card col-left row-3">
  <div class="line center" style="top:68px;font-size:70px;line-height:80px">The Support<br>System</div>
  <div class="line rose center" style="top:232px;font-size:58px;line-height:62px">You've Been<br>Missing</div>
  <div class="cta" style="top:441px"><span>Stay Consistent with</span><em>RT in Your Pocket!</em></div>
</section>

<section class="card col-right row-3">
  <div class="line" style="left:44px;top:14px;font-size:86px;line-height:96px;font-style:italic">Support</div>
  <div class="line" style="left:44px;top:100px;font-size:66px;line-height:71px;color:var(--rose)">When<br>Motivation<br>Disappears</div>
  <div class="photo photo-pair" style="left:0;right:0;top:316px;bottom:0" role="img" aria-label="Two women laughing together in denim jackets"></div>
  <div class="side-band">Stay<br>Consistent<br>with<br><em style="color:var(--cta-rose)">RT in Your<br>Pocket!</em></div>
</section>

<section class="card col-left row-4">
  <div class="photo photo-portrait" style="left:290px;top:160px;width:204px;height:316px" role="img" aria-label="Smiling coach in a dark lace top"></div>
  <div class="line" style="left:30px;top:38px;font-size:66px;line-height:80px">What if</div>
  <div class="line" style="left:30px;top:124px;font-size:46px;line-height:56px">Checked in</div>
  <div class="line rose" style="left:310px;top:38px;font-size:118px;line-height:150px">RT</div>
  <div class="line rose" style="left:26px;top:184px;font-size:94px;line-height:94px">Every<br>Day?</div>
  <div class="cta" style="top:472px"><span>Stay Consistent with</span><em>RT in Your Pocket!</em></div>
</section>

<section class="card col-right row-4">
  <div class="line center" style="top:52px;font-size:72px;line-height:88px">The Missing<br>Piece Isn't</div>
  <div class="line rose center" style="top:226px;font-size:96px;line-height:92px">Another<br>Diet</div>
  <div class="cta" style="top:450px"><span>Stay Consistent with</span><em>RT in Your Pocket!</em></div>
</section>

<section class="card col-left row-5">
  <div class="line rose center" style="top:38px;font-size:70px;line-height:76px">Eat the food<br>you love.</div>
  <div class="line center" style="top:216px;font-size:58px;line-height:60px">Stay<br>Accountable<br>Every day</div>
  <div class="cta" style="top:443px"><span>Stay Consistent with</span><em>RT in Your Pocket!</em></div>
</section>

<section class="card col-right row-5">
  <div class="line rose center" style="top:74px;font-size:58px;line-height:68px">One Bad Meal</div>
  <div class="line center" style="top:144px;font-size:58px;line-height:68px">Doesn't Mean<br>You Failed</div>
  <div class="photo photo-pair" style="left:0;right:0;top:270px;height:278px" role="img" aria-label="Two women laughing together in denim jackets"></div>
  <div class="band"><span>Stay Consistent with&nbsp;<em>RT in Your Pocket!</em></span></div>
</section>

</body>
</html>
```